LEARN Business Skills so you can Earn a good living

size of the poster is 8”x 10.75" plus 0.25" bleed.
Please leave 1 inch on the bottoum for footer
I want a design a poster that will attract people's attention.
I appreciate a creative ad however the ad should not take away from being able to clearly read the text.
-I also appreciate a simple creative ad that is not too busy.
-you can use graphics, vectors, or pictures of real people.
-however, if you use real people it should be a white male that is wearing a white shirt and look like a professional person.

Target Market(s)

Potential young business people

Industry/Entity Type

education

Requirements
Must have
• easy to read the text
Nice to have
• I would like a "creative" simple ad that is easy to be read
Should not have
• pictures of women

```html
<!DOCTYPE html>
<html lang="en">
<head>
<meta charset="UTF-8">
<title>Learn IT to Earn IT – Business Enrichment Course</title>
<link rel="stylesheet" href="https://fonts.googleapis.com/css2?family=Poppins:wght@400;600;700&family=Roboto:wght@400;500&display=swap">
<style>
  :root {
    --paper: #f7f9fa;
    --ink: #0d0d0d;
    --text: #1f1f1f;
    --accent: #c8202f;
    --gold-light: #d6b35e;
    --gold-deep: #a47c2c;
    --silver: #cfccc4;
    --dot-grey: #e6e9eb;
  }
  * { margin: 0; padding: 0; box-sizing: border-box; }
  html, body { width: 900px; height: 1200px; overflow: hidden; background: var(--paper); }
  .poster {
    position: relative;
    width: 900px;
    height: 1200px;
    overflow: hidden;
    background: var(--paper);
    font-family: "Roboto", Arial, sans-serif;
    color: var(--text);
  }
  .dot-field {
    position: absolute;
    top: 150px;
    left: 50px;
    width: 800px;
    height: 690px;
    background: radial-gradient(ellipse at 50% 50%, var(--dot-grey) 0%, rgba(230,233,235,0.7) 45%, rgba(247,249,250,0) 72%);
  }
  .headline {
    position: absolute;
    top: 88px;
    left: 0;
    width: 100%;
    text-align: center;
    font-family: "Poppins", Arial, sans-serif;
    font-weight: 700;
    font-size: 82px;
    line-height: 1;
    letter-spacing: -1px;
    color: var(--ink);
  }
  .course-name {
    position: absolute;
    top: 178px;
    left: 0;
    width: 100%;
    display: flex;
    justify-content: center;
    align-items: center;
    gap: 10px;
    font-family: "Poppins", Arial, sans-serif;
    font-size: 29px;
    color: var(--ink);
  }
  .course-name svg { width: 18px; height: 24px; }
  .hero-photo {
    position: absolute;
    top: 250px;
    left: 190px;
    width: 520px;
    height: 405px;
    border-radius: 50%;
    background: radial-gradient(ellipse at 50% 50%, var(--silver) 0%, var(--gold-light) 40%, var(--gold-deep) 85%);
  }
  .quote {
    position: absolute;
    top: 680px;
    left: 0;
    width: 100%;
    display: flex;
    justify-content: center;
    align-items: center;
  }
  .quote-mark { width: 66px; height: 58px; flex: none; }
  .quote-mark.open { margin-right: 34px; }
  .quote-mark.close { margin-left: 44px; }
  .quote-text {
    font-family: "Roboto", Arial, sans-serif;
    font-weight: 500;
    font-size: 40px;
    line-height: 49px;
    text-align: center;
    color: var(--ink);
  }
  .benefits-title {
    position: absolute;
    top: 823px;
    left: 0;
    width: 100%;
    text-align: center;
    font-family: "Poppins", Arial, sans-serif;
    font-weight: 600;
    font-size: 26px;
    color: var(--accent);
  }
  .benefits {
    position: absolute;
    top: 861px;
    left: 0;
    width: 100%;
    text-align: center;
    font-weight: 500;
    font-size: 21px;
    color: var(--ink);
    word-spacing: 1px;
  }
  .benefits .sep { margin: 0 9px; }
  .divider {
    position: absolute;
    top: 931px;
    left: 380px;
    width: 140px;
    height: 2px;
    background: var(--ink);
    border-radius: 1px;
  }
  .topics {
    position: absolute;
    top: 968px;
    list-style: none;
    font-size: 15.5px;
    line-height: 19.4px;
    color: var(--text);
  }
  .topics li { position: relative; padding-left: 12px; }
  .topics li::before {
    content: "";
    position: absolute;
    left: 0;
    top: 6px;
    width: 5px;
    height: 5px;
    border-radius: 50%;
    background: var(--accent);
  }
  .topics li.no-bullet::before { display: none; }
  .col-1 { left: 64px; }
  .col-2 { left: 327px; }
  .col-3 { left: 522px; }
  .col-4 { left: 728px; }
</style>
</head>
<body>
<main class="poster">
  <div class="dot-field" role="img" aria-label="Soft grey halftone dot pattern behind the photo"></div>

  <h1 class="headline">Learn IT to Earn IT</h1>

  <p class="course-name">
    <svg viewBox="0 0 18 24" aria-hidden="true"><path d="M2 3 L7 3 L16 12 L7 21 L2 21 L10 12 Z" fill="var(--accent)"/></svg>
    Business Enrichment Course
    <svg viewBox="0 0 18 24" aria-hidden="true"><path d="M16 3 L11 3 L2 12 L11 21 L16 21 L8 12 Z" fill="var(--accent)"/></svg>
  </p>

  <div class="hero-photo" role="img" aria-label="Photo of a small figurine of a man standing on a stack of gold and silver coins"></div>

  <div class="quote">
    <svg class="quote-mark open" viewBox="0 0 66 58" aria-hidden="true">
      <path d="M26 4 C10 12 2 26 4 40 C5 50 11 56 19 56 C26 56 31 51 31 44 C31 37 26 33 20 33 C16 33 14 34 13 35 C13 24 19 14 29 8 Z" fill="var(--accent)"/>
      <path d="M60 4 C44 12 36 26 38 40 C39 50 45 56 53 56 C60 56 65 51 65 44 C65 37 60 33 54 33 C50 33 48 34 47 35 C47 24 53 14 63 8 Z" fill="var(--accent)"/>
    </svg>
    <p class="quote-text">A proven success of helping<br>people in their livelihoods</p>
    <svg class="quote-mark close" viewBox="0 0 66 58" aria-hidden="true">
      <path d="M6 54 C22 46 30 32 28 18 C27 8 21 2 13 2 C6 2 1 7 1 14 C1 21 6 25 12 25 C16 25 18 24 19 23 C19 34 13 44 3 50 Z" fill="var(--accent)"/>
      <path d="M40 54 C56 46 64 32 62 18 C61 8 55 2 47 2 C40 2 35 7 35 14 C35 21 40 25 46 25 C50 25 52 24 53 23 C53 34 47 44 37 50 Z" fill="var(--accent)"/>
    </svg>
  </div>

  <h2 class="benefits-title">Business skills that will help you</h2>
  <p class="benefits">Get A Quality Job<span class="sep">|</span>Start/grow Your Business<span class="sep">|</span>Increase Your Salary</p>

  <div class="divider"></div>

  <ul class="topics col-1">
    <li>Business Admnistration</li>
    <li>Small&nbsp; Business Management</li>
    <li>Finance</li>
    <li>Investments</li>
    <li>Computers</li>
    <li>Accounting</li>
  </ul>
  <ul class="topics col-2">
    <li>Sales</li>
    <li>Marketing</li>
    <li>Project Management</li>
    <li class="no-bullet">Interviewing Skills</li>
    <li>Business Law</li>
    <li>Negotiation</li>
  </ul>
  <ul class="topics col-3">
    <li>Public Speaking</li>
    <li>Import/export</li>
    <li>Information Technoloy</li>
    <li>Distribution</li>
    <li>Marketing</li>
    <li>Ledgerly</li>
  </ul>
  <ul class="topics col-4">
    <li>Real Estate</li>
    <li>Health Care</li>
    <li>Management</li>
    <li>Shopvale</li>
  </ul>
</main>
</body>
</html>
```